Tech business card design

We need an amazing business card design for our new business 'Pexla' a marketing tech startup based in Sydney, Australia. We provide an online marketplace for businesses to search and buy advertising media, connect with service providers and learn more about marketing. We wish to communicate 'cool tech', reliability and professionalism and design based around our logo.

Target Market(s)

Business Owners

Contact Information for Business Card

Name
Position
Email Address
Website
Phone Number

Font styles to use
Other font styles liked:
• Avenir & Avenir Next

Colors

Designer to choose colors to be used in the design.

```html
<!DOCTYPE html>
<html lang="en">
<head>
<meta charset="utf-8">
<title>Pexla Business Card</title>
<link rel="stylesheet" href="https://fonts.googleapis.com/css2?family=Open+Sans:wght@400;600;700;800&display=swap">
<style>
  :root {
    --backdrop: #e2dfdf;
    --navy: #222647;
    --navy-glow: #353c68;
    --ink: #1b1e45;
    --text-grey: #4a4a4a;
    --white: #ffffff;
    --edge: #7a7a7a;
  }
  * { box-sizing: border-box; margin: 0; padding: 0; }
  html, body {
    width: 975px; height: 1200px; overflow: hidden;
    background: var(--backdrop);
    font-family: "Open Sans", Arial, sans-serif;
  }
  .canvas { position: relative; width: 975px; height: 1200px; }

  /* Front */
  .card-front {
    position: absolute; left: 57px; top: 83px; width: 861px; height: 491px;
    border: 1px solid var(--edge); background: var(--white); display: flex;
  }
  .contact-side { position: relative; width: 433px; height: 100%; }
  .person-name {
    position: absolute; left: 71px; top: 108px;
    font-size: 28px; font-weight: 700; color: var(--ink); letter-spacing: 0.2px;
  }
  .person-role {
    position: absolute; left: 71px; top: 143px;
    font-size: 24px; color: var(--ink);
  }
  .contact-list {
    position: absolute; left: 71px; top: 201px; list-style: none;
    font-size: 21px; color: var(--text-grey);
  }
  .contact-list li { display: flex; align-items: center; height: 33px; }
  .contact-list svg { width: 21px; height: 21px; margin-right: 9px; flex: none; }
  .address {
    position: absolute; left: 71px; top: 322px;
    font-size: 21px; line-height: 29px; color: var(--text-grey);
  }
  .brand-side {
    position: relative; flex: 1; background: var(--navy);
    display: flex; align-items: center; justify-content: center;
  }
  .brand-side::before {
    content: ""; position: absolute; left: 0; top: 40px; bottom: 20px; width: 42px;
    background: linear-gradient(90deg, rgba(70,78,130,0) 0%, rgba(70,78,130,0.7) 55%, rgba(70,78,130,0) 100%);
    -webkit-mask: linear-gradient(180deg, transparent, #000 35%, #000 65%, transparent);
    mask: linear-gradient(180deg, transparent, #000 35%, #000 65%, transparent);
  }
  .wordmark {
    position: relative; color: var(--white); font-weight: 800;
    letter-spacing: -2px; line-height: 1;
  }
  .brand-side .wordmark { font-size: 112px; margin-left: 20px; margin-top: -30px; }

  /* Back */
  .card-back {
    position: absolute; left: 58px; top: 619px; width: 859px; height: 428px;
    background: var(--navy); display: flex; align-items: center; justify-content: center;
  }
  .card-back .wordmark { font-size: 150px; margin-top: -70px; }
  .back-band {
    position: absolute; left: 58px; top: 1005px; width: 859px; height: 42px;
    border-top: 1px solid #8a8fad;
    background: radial-gradient(ellipse 45% 140% at 50% 50%, var(--navy-glow) 0%, var(--navy) 100%);
  }
  .web-strip {
    position: absolute; left: 61px; top: 1049px; width: 854px; height: 60px;
    background: var(--white); border: 2px solid #111;
    display: flex; align-items: center; justify-content: center;
    font-size: 28px; letter-spacing: 4px; color: var(--ink);
  }
</style>
</head>
<body>
<div class="canvas">
  <section class="card-front">
    <div class="contact-side">
      <h1 class="person-name">MARA QUINLAN</h1>
      <p class="person-role">Position</p>
      <ul class="contact-list">
        <li>
          <svg viewBox="0 0 24 24" aria-hidden="true"><circle cx="12" cy="12" r="10.5" fill="none" stroke="#1b1e45" stroke-width="2"/><path d="M8.3 6.5l2 2.6-1.2 1.5c.8 1.7 2.1 3 3.8 3.8l1.5-1.2 2.6 2-1.1 1.8c-4.4-.4-8.6-4.6-9-9z" fill="#1b1e45"/></svg>
          012-345-6789
        </li>
        <li>
          <svg viewBox="0 0 24 24" aria-hidden="true"><rect x="2" y="5" width="20" height="14" fill="#1b1e45"/><path d="M2.5 5.5l9.5 8 9.5-8M2.5 18.5l7-6.5M21.5 18.5l-7-6.5" stroke="#fff" stroke-width="1.6" fill="none"/></svg>
          info@pexla.com
        </li>
        <li>
          <svg viewBox="0 0 24 24" aria-hidden="true" fill="none" stroke="#1b1e45" stroke-width="1.6"><circle cx="12" cy="12" r="10"/><ellipse cx="12" cy="12" rx="4.5" ry="10"/><path d="M2 12h20M3.5 7h17M3.5 17h17M12 2v20"/></svg>
          www.pexla.com
        </li>
      </ul>
      <p class="address">Street name City Name,<br>Zipcode,012345</p>
    </div>
    <div class="brand-side">
      <span class="wordmark">pexla</span>
    </div>
  </section>

  <section class="card-back">
    <span class="wordmark">pexla</span>
  </section>
  <div class="back-band"></div>
  <div class="web-strip">www.pexla.com</div>
</div>
</body>
</html>
```